Quiet Braising For The Patient Epicure

Hi, I had a book cover designed on this site, but I want to modify the cover and change the colours. I want to keep the slow cooker and the ingredients on the cover, but I want to simplify it a bit. And, I am open to other ideas. I have attached below a book cover idea I like and I like the colors as well. I want it to be called Quiet Braising, with the language on the right corner: "Curated For Nearly Effortless Meals That Are Greater Than The Sum Of Their Ingredients" I like the circles idea and my name as the author on the curve.

Target Market(s)

Home Cooks

Colors
00AB8E
00BBA5
67D7C9
C6EFE9
E9F9F6
F0912C
F2A743
F7CA91
FBE8D2
FDF5EE
E54698
E96AAD
F1A4CE
F9D9EA
FCEFF6
6B429C
8869AF
B7A5CE
E3DAEB
F3F0F8

Requirements
Must have
• Please use the colors on the Harvest Table Cook Book and I like the design, but I do not want it identical. I like the author name (Marcus T. Hallbright) on the side of the circle on the upper right side of the cover.
Nice to have
• I like the large words "Quiet Braising"

```html
<!DOCTYPE html>
<html lang="en">
<head>
<meta charset="utf-8">
<title>Quiet Braising — Book Cover</title>
<link href="https://fonts.googleapis.com/css2?family=Playfair+Display:wght@400;700&display=swap" rel="stylesheet">
<style>
  :root {
    --backdrop: #2a2a2a;
    --cover: #2a2b35;
    --gold: #d9b23e;
    --gold-light: #e9bd3f;
    --white: #ffffff;
    --magenta: rgba(201, 32, 106, 0.95);
    --coral: rgba(226, 84, 96, 0.92);
    --orange: rgba(240, 154, 44, 0.85);
    --leaf-light: rgba(163, 177, 94, 0.9);
    --leaf-dark: rgba(63, 138, 92, 0.88);
    --clear: rgba(42, 43, 53, 0);
  }
  * { margin: 0; padding: 0; box-sizing: border-box; }
  html, body { width: 1200px; height: 1200px; overflow: hidden; background: var(--backdrop); }
  .cover {
    position: absolute; left: 216px; top: 24px; width: 768px; height: 1152px;
    background: var(--cover); overflow: hidden;
    font-family: "Playfair Display", serif;
  }
  .botanical-art {
    position: absolute; inset: 0;
    background:
      radial-gradient(ellipse 210px 300px at 120px 330px, var(--magenta) 0%, var(--magenta) 45%, var(--clear) 100%),
      radial-gradient(ellipse 70px 120px at 10px 230px, var(--orange) 0%, var(--clear) 100%),
      radial-gradient(ellipse 170px 70px at 430px 40px, var(--orange) 0%, var(--clear) 100%),
      radial-gradient(ellipse 190px 210px at 700px 170px, var(--coral) 0%, var(--coral) 40%, var(--clear) 100%),
      radial-gradient(ellipse 180px 300px at 70px 820px, var(--leaf-light) 0%, var(--leaf-light) 40%, var(--clear) 100%),
      radial-gradient(ellipse 220px 120px at 680px 640px, var(--leaf-dark) 0%, var(--leaf-dark) 35%, var(--clear) 100%);
  }
  .food-table {
    position: absolute; left: 0; right: 0; bottom: 0; height: 240px;
    background: linear-gradient(180deg, rgba(42,43,53,0) 0%, #9c4a32 22%, #b5773f 45%, #c98a52 58%, #8a5a33 72%, #e6dcc8 82%, #efe7d6 100%);
  }
  .author {
    position: absolute; left: 290px; top: 244px;
    color: var(--white); font-size: 30px; font-weight: 400; letter-spacing: 0.5px;
    white-space: nowrap;
  }
  .title-line { position: absolute; line-height: 1; font-weight: 400; white-space: nowrap; }
  .title-quiet { right: 60px; top: 258px; font-size: 188px; color: var(--gold); letter-spacing: -4px; }
  .title-braising { right: 34px; top: 419px; font-size: 186px; color: var(--white); letter-spacing: -5px; }
  .tagline {
    position: absolute; right: 32px; top: 758px; width: 300px; text-align: right;
    font-size: 21px; line-height: 30px; color: var(--white);
  }
  .tagline strong { color: var(--gold-light); font-weight: 700; }
</style>
</head>
<body>
  <main class="cover">
    <div class="botanical-art" role="img" aria-label="Botanical illustration of magenta and coral flowers, orange buds, vines and green leaves"></div>
    <div class="food-table" role="img" aria-label="Illustration of a slow cooker, copper pot, wine bottles, bread, vegetables, fish, cheese and roast chicken on a wooden table"></div>

    <p class="author">Marcus T. Hallbright</p>
    <h1>
      <span class="title-line title-quiet">Quiet</span>
      <span class="title-line title-braising">Braising</span>
    </h1>
    <p class="tagline"><strong>Curated For Nearly<br>Effortless Meals</strong> That Are<br>Greater Than The Sum Of<br>Their Ingredients</p>
  </main>
</body>
</html>
```